Need Business Card for our Real Estate Business with Sales Executive's Picture

PANTONE 484 C ( RED)

PANTONE 2766 C ( BLUE

Industry/Entity Type

Real Estate

Contact Information for Business Card

Name, Mobile, email, & picture of Person
Agency Phone, address, Web address

Requirements
Must have
• Our Logo Colours, Agent Picture,

```html
<!DOCTYPE html>
<html lang="en">
<head>
<meta charset="UTF-8">
<title>Meridian Real Estate – Business Card</title>
<link href="https://fonts.googleapis.com/css2?family=Cinzel:wght@500&family=Josefin+Sans:wght@400;600&display=swap" rel="stylesheet">
<style>
  :root {
    --stage: #161616;
    --brand-red: #8c1222;
    --brand-red-dark: #6e0c19;
    --brand-blue: #1f2b62;
    --brand-blue-deep: #141c48;
    --paper: #ffffff;
    --paper-shade: #eeeeee;
    --ink-light: #f2f3f8;
    --photo-light: #e9e6e2;
    --photo-suit: #2c4a8c;
  }
  * { box-sizing: border-box; margin: 0; padding: 0; }
  html, body { width: 1200px; height: 864px; overflow: hidden; background: var(--stage); }
  .stage {
    width: 1200px; height: 864px;
    display: flex; align-items: center; justify-content: center; gap: 56px;
  }
  .card {
    position: relative; width: 520px; height: 298px; overflow: hidden;
    border-radius: 3px; box-shadow: 0 18px 40px rgba(0,0,0,.6);
  }

  /* Front */
  .card--front { background: linear-gradient(160deg, var(--brand-blue) 40%, var(--brand-blue-deep)); }
  .front__header {
    position: absolute; left: 0; top: 0; width: 100%; height: 104px;
    background: linear-gradient(180deg, var(--paper) 70%, var(--paper-shade));
  }
  .front__rule {
    position: absolute; left: 0; width: 100%; height: 4px; background: var(--brand-red);
  }
  .front__rule--upper { top: 80px; }
  .front__rule--lower { top: 98px; height: 5px; }
  .front__gap { position: absolute; left: 0; top: 104px; width: 100%; height: 6px; background: var(--paper); }
  .agent-photo {
    position: absolute; left: 34px; top: 34px; width: 118px; height: 118px; border-radius: 50%;
    border: 3px solid var(--brand-blue);
    background: radial-gradient(circle at 50% 85%, var(--photo-suit) 0 38%, transparent 39%),
                radial-gradient(circle at 50% 40%, var(--photo-light), #cfcac4);
  }
  .agent-name {
    position: absolute; left: 236px; top: 52px;
    font: 500 21px/1 "Cinzel", serif; letter-spacing: 1px; color: var(--brand-red);
  }
  .contact {
    position: absolute; left: 266px; top: 134px; list-style: none;
    font: 400 14px/1 "Josefin Sans", sans-serif; color: var(--ink-light); letter-spacing: .5px;
  }
  .contact li { display: flex; align-items: center; gap: 10px; height: 19px; }
  .contact svg { width: 12px; height: 12px; fill: var(--ink-light); flex: none; }
  .address {
    position: absolute; left: 266px; top: 232px;
    font: 400 14px/1.3 "Josefin Sans", sans-serif; color: var(--ink-light); letter-spacing: .5px;
  }
  .brand {
    position: absolute; display: flex; align-items: center; gap: 10px;
    font: 400 22px/1.15 "Cinzel", serif; color: var(--ink-light); letter-spacing: 2px;
    white-space: nowrap;
  }
  .brand__mark { width: 10px; height: 10px; background: var(--ink-light); flex: none; }
  .brand__name { text-align: center; }
  .card--front .brand { left: 36px; top: 206px; font-size: 18px; }

  /* Back */
  .card--back { background: linear-gradient(160deg, var(--brand-blue) 40%, var(--brand-blue-deep)); }
  .back__top {
    position: absolute; left: 0; top: 0; width: 100%; height: 96px;
    background: linear-gradient(180deg, var(--brand-red), var(--brand-red-dark));
  }
  .back__band { position: absolute; left: 0; top: 96px; width: 100%; height: 14px; background: var(--paper); }
  .card--back .brand { left: 50%; top: 174px; transform: translateX(-50%); font-size: 26px; }
</style>
</head>
<body>
<main class="stage">
  <section class="card card--front" aria-label="Business card front">
    <div class="front__header"></div>
    <div class="front__rule front__rule--upper"></div>
    <div class="front__rule front__rule--lower"></div>
    <div class="front__gap"></div>
    <div class="agent-photo" role="img" aria-label="Portrait photo of the sales executive"></div>
    <h1 class="agent-name">Daniel Reyes</h1>
    <ul class="contact">
      <li><svg viewBox="0 0 24 24"><path d="M6.6 10.8a15 15 0 0 0 6.6 6.6l2.2-2.2a1 1 0 0 1 1-.25 11.4 11.4 0 0 0 3.6.6 1 1 0 0 1 1 1V20a1 1 0 0 1-1 1A17 17 0 0 1 3 4a1 1 0 0 1 1-1h3.5a1 1 0 0 1 1 1c0 1.250.2 2.45.6 3.6a1 1 0 0 1-.25 1z"/></svg>(09) 555 0142</li>
      <li><svg viewBox="0 0 24 24"><path d="M7 1h10a2 2 0 0 1 2 2v18a2 2 0 0 1-2 2H7a2 2 0 0 1-2-2V3a2 2 0 0 1 2-2zm0 3v14h10V4zm5 15.5a1 1 0 1 0 0 2 1 1 0 0 0 0-2z"/></svg>027 555 0198</li>
      <li><svg viewBox="0 0 24 24"><path d="M2 5h20v14H2zm2 2v.4l8 5.2 8-5.2V7zm0 2.8V17h16V9.8l-8 5.2z"/></svg>daniel@meridianestates.com</li>
      <li><svg viewBox="0 0 24 24"><path d="M12 2a10 10 0 1 0 0 20 10 10 0 0 0 0-20zm6.9 6h-3a15 15 0 0 0-1.3-3.6A8 8 0 0 1 18.9 8zM12 4c.8 1.2 1.5 2.5 1.9 4h-3.8c.4-1.5 1.1-2.8 1.9-4zM4.3 14a8 8 0 0 1 0-4h3.4a16 16 0 0 0 0 4zm.8 2h3a15 15 0 0 0 1.3 3.6A8 8 0 0 1 5.1 16zm3-8h-3a8 8 0 0 1 4.3-3.6A15 15 0 0 0 8.1 8zM12 20c-.8-1.2-1.5-2.5-1.9-4h3.8c-.4 1.5-1.1 2.8-1.9 4zm2.3-6H9.7a14 14 0 0 1 0-4h4.6a14 14 0 0 1 0 4zm.3 5.6a15 15 0 0 0 1.3-3.6h3a8 8 0 0 1-4.3 3.6zm1.7-5.6a16 16 0 0 0 0-4h3.4a8 8 0 0 1 0 4z"/></svg>www.meridianestates.com</li>
    </ul>
    <p class="address">820 Harbor Lane Suite 300<br>Lakeview, IL 60614</p>
    <div class="brand"><span class="brand__mark"></span><span class="brand__name">Meridian<br>Real Estate</span></div>
  </section>

  <section class="card card--back" aria-label="Business card back">
    <div class="back__top"></div>
    <div class="back__band"></div>
    <div class="brand"><span class="brand__mark"></span><span class="brand__name">Meridian<br>Real Estate</span></div>
  </section>
</main>
</body>
</html>
```